VELMOR Website Design

We need a website designed for our company VELMOR. We are a luxury lifestyle club that will provide benefits and services for our members. The site should be clean & sleek, preferably using black and white (or darker colors). (example sites: stravenhall.example, plinth.example)

Here is a link of a sample page I did using wix. (https://dunmere7.sitehostly.example/mysite) This can be used to get a general idea.

Target Market(s)

Upper Middle Class in the United States

Number of Pages Required

5+ page

Font styles to use
Sans Serif
Other font styles liked:
• Arial (or other similar fonts)

Requirements
Must have
• A clean design that is eye-catching and speaks to our company.
Nice to have
• Ideas for copy.

```html
<!DOCTYPE html>
<html lang="en">
<head>
<meta charset="utf-8">
<title>VELMOR — Luxury Lifestyle Club</title>
<link href="https://fonts.googleapis.com/css2?family=Montserrat:ital,wght@0,400;0,600;0,700;1,600&family=Open+Sans:wght@400;600;700&display=swap" rel="stylesheet">
<style>
:root{
  --bg:#1c1c1c;
  --bg-2:#242424;
  --bg-3:#2e2e2e;
  --panel:#151515;
  --blue:#1668f0;
  --blue-light:#3d86ff;
  --white:#ffffff;
  --grey:#b5b5b5;
  --grey-2:#8a8a8a;
  --line:#3a3a3a;
}
*{margin:0;padding:0;box-sizing:border-box}
html,body{width:1200px;height:3440px;overflow:hidden;background:var(--bg);color:var(--white);font-family:"Open Sans",Arial,sans-serif}
.page{position:relative;width:1200px;height:3440px}
h1,h2,h3,h4{font-family:"Montserrat",Arial,sans-serif}

/* hero */
.hero{position:relative;height:640px;overflow:hidden}
.hero-photo{position:absolute;inset:0;background:linear-gradient(160deg,#4a5560 0%,#2c3339 45%,#1a1d20 100%)}
.hero-shade{position:absolute;inset:0;background:rgba(0,0,0,.35)}
.nav{position:absolute;top:0;left:0;right:0;height:92px;display:flex;align-items:center;justify-content:space-between;padding:0 120px}
.logo{font-family:"Montserrat",Arial,sans-serif;font-weight:600;font-size:40px;letter-spacing:3px;color:var(--white);border:3px solid var(--white);padding:2px 14px;line-height:52px}
.nav-links{display:flex;gap:34px;align-items:center;font-size:15px;font-weight:600}
.nav-links a{color:var(--white);text-decoration:none}
.nav-links a.active{color:var(--blue-light)}
.nav-search{width:24px;height:24px;border-radius:50%;background:var(--blue)}
.hero-title{position:absolute;left:116px;top:282px;width:980px;font-size:38px;line-height:52px;font-weight:700;letter-spacing:1px;text-transform:uppercase}
.hero-arrow{position:absolute;top:380px}
.hero-arrow.left{left:22px}
.hero-arrow.right{right:22px}
.hero-dots{position:absolute;left:584px;top:574px;display:flex;gap:8px}
.hero-dots span{width:12px;height:12px;border-radius:50%;background:var(--white);opacity:.5}
.hero-dots span.on{background:var(--blue-light);opacity:1}

/* section title band */
.band-title{text-align:center;background:var(--bg-2)}
.band-title h2{font-size:46px;font-weight:600;letter-spacing:1px;text-transform:uppercase}
.band-title .rule{width:100%;height:1px;background:var(--line)}
.about-head{height:120px;padding-top:34px}
.tabs{height:60px;background:var(--panel);display:flex;justify-content:center;gap:4px;align-items:center}
.tabs span{font-size:13px;padding:8px 34px;background:var(--bg-3);color:var(--grey)}
.tabs span.active{background:#3a3a3a;color:var(--white)}

/* about */
.about{height:420px;background:var(--bg);display:flex;padding:40px 112px 0;gap:40px}
.about-left{width:480px}
.about-photo{height:160px;background:linear-gradient(135deg,#3a6f9a 0%,#b9a07a 55%,#4f6a3a 100%)}
.about-left h3{font-size:24px;font-weight:600;margin:36px 0 12px;letter-spacing:1px}
.about-left p{font-size:13px;line-height:20px;color:var(--grey)}
.about-list{flex:1;display:flex;flex-direction:column;gap:46px;padding-top:4px}
.about-item{display:flex;gap:26px;align-items:flex-start}
.circle-icon{flex:0 0 52px;height:52px;border-radius:50%;background:var(--blue);display:flex;align-items:center;justify-content:center}
.about-item h4{font-size:13px;color:var(--blue-light);font-weight:600;margin:4px 0 8px;text-transform:uppercase}
.about-item p{font-size:13px;line-height:20px;color:var(--grey)}

/* team */
.team{height:940px;background:var(--bg-2);padding-top:64px;text-align:center}
.team h2{font-size:46px;font-weight:600;letter-spacing:1px}
.team .lead{font-family:"Montserrat",Arial,sans-serif;font-style:italic;font-weight:600;font-size:22px;margin-top:16px;color:#e6e6e6}
.team-grid{display:grid;grid-template-columns:repeat(3,308px);gap:24px 22px;justify-content:center;margin-top:48px}
.member{height:342px;background:var(--panel);position:relative}
.member-photo{height:186px;background:linear-gradient(180deg,#55595e 0%,#34373b 100%)}
.member .up{position:absolute;left:128px;top:160px;width:52px;height:52px;border-radius:50%;background:var(--blue);display:flex;align-items:center;justify-content:center}
.member h4{font-size:14px;font-weight:700;margin-top:42px;text-transform:uppercase}
.member p{font-size:12px;line-height:18px;color:var(--grey);padding:10px 30px 0}
.member.featured{background:var(--blue)}
.member.featured .up{background:var(--panel)}
.member.featured p{color:#e3ecff}
.socials{display:flex;gap:8px;justify-content:center;margin-top:10px}
.socials span{width:22px;height:22px;border-radius:50%;background:var(--white)}

/* membership */
.membership{position:relative;height:450px;overflow:hidden;text-align:center}
.membership-photo{position:absolute;inset:0;background:linear-gradient(180deg,#2a2f33 0%,#3c4a52 60%,#1d2327 100%)}
.membership .shade{position:absolute;inset:0;background:rgba(0,0,0,.45)}
.membership .inner{position:relative;padding-top:132px}
.membership h3{font-size:30px;font-weight:700;letter-spacing:2px}
.membership h2{font-size:30px;font-weight:700;letter-spacing:1px;line-height:44px;margin-top:14px;text-transform:uppercase}
.btn{display:inline-block;margin-top:36px;padding:10px 34px;border:2px solid var(--white);font-size:13px;font-weight:600;letter-spacing:1px}

/* testimonials */
.testi-head{height:160px;padding-top:42px}
.testi-head h2{font-size:34px;letter-spacing:1px}
.testi-head .lead{font-family:"Montserrat",Arial,sans-serif;font-style:italic;font-weight:600;font-size:20px;margin-top:14px}
.testimonial{position:relative;height:380px;background:var(--bg)}
.testi-photo{position:absolute;left:0;top:0;width:380px;height:280px;background:linear-gradient(180deg,#a46f45 0%,#d5a063 40%,#34404a 100%)}
.testi-quote{position:absolute;left:410px;top:30px;width:750px;font-size:20px;line-height:32px;font-weight:600}
.roles{position:absolute;left:0;right:0;top:280px;height:100px;background:var(--bg-3);display:flex}
.role{width:380px;text-align:center;padding-top:22px}
.role small{display:block;font-size:10px;color:var(--grey);text-transform:uppercase;letter-spacing:1px}
.role strong{display:block;font-family:"Montserrat",Arial,sans-serif;font-size:28px;font-weight:600;margin-top:6px;text-transform:uppercase}
.role.active{background:var(--blue)}
.role.active small{color:#dbe6ff}

/* footer */
.footer{height:180px;background:var(--panel);display:flex;padding:34px 120px 0;gap:70px}
.footer-col{width:300px;font-size:12px;line-height:19px;color:var(--grey)}
.footer-col h4{font-size:12px;color:var(--white);margin-bottom:8px;text-transform:uppercase;letter-spacing:1px}
.footer-socials{display:flex;gap:8px;margin-top:12px}
.footer-socials span{width:26px;height:26px;border-radius:50%;border:1px solid var(--grey-2)}
.subscribe{margin-top:10px;display:flex}
.subscribe span{flex:1;height:30px;background:var(--bg-3);color:var(--grey-2);font-size:11px;padding:6px 10px}
.subscribe b{width:34px;height:30px;background:var(--blue)}
.bottom-bar{height:40px;background:#0d0d0d;display:flex;justify-content:center;align-items:center}
</style>
</head>
<body>
<div class="page">

  <header class="hero">
    <div class="hero-photo" role="img" aria-label="Business meeting at a desk with documents and a pen, dark toned"></div>
    <div class="hero-shade"></div>
    <nav class="nav">
      <div class="logo">VELMOR</div>
      <div class="nav-links">
        <a class="active" href="#">Home</a>
        <a href="#">About us</a>
        <a href="#">Services &amp; Benefits</a>
        <a href="#">Contact</a>
        <span class="nav-search"></span>
      </div>
    </nav>
    <svg class="hero-arrow left" width="24" height="40" viewBox="0 0 24 40"><path d="M20 4 4 20l16 16" fill="none" stroke="#fff" stroke-width="4"/></svg>
    <h1 class="hero-title">Receive access to the best accountants, attorneys, real estate agents, private bankers/advisers and more!</h1>
    <svg class="hero-arrow right" width="24" height="40" viewBox="0 0 24 40"><path d="M4 4l16 16L4 36" fill="none" stroke="#fff" stroke-width="4"/></svg>
    <div class="hero-dots"><span class="on"></span><span></span></div>
  </header>

  <section class="band-title about-head">
    <h2>About us</h2>
  </section>
  <div class="tabs"><span class="active">Services</span><span>Experiences</span><span>About VELMOR</span></div>

  <section class="about">
    <div class="about-left">
      <div class="about-photo" role="img" aria-label="Luxury villa with pool and palm trees at dusk"></div>
      <h3>LIFESTYLE CLUB</h3>
      <p>Lorem ipsum dolor sit amet, consectetur adipiscing elit. Aenean sagittis est nec orci facilisis, vel pretium nibh tempor. Praesent varius felis ut lorem dictum, in iaculis metus tincidunt. Nullam quis velit nec lacus fermentum sodales non at nunc. Sed at magna congue.</p>
    </div>
    <div class="about-list">
      <div class="about-item">
        <span class="circle-icon"><svg width="20" height="14" viewBox="0 0 20 14"><path d="M2 12 10 4l8 8" fill="none" stroke="#fff" stroke-width="3"/></svg></span>
        <div><h4>Benefits and services</h4><p>VELMOR membership provides you with amazing benefits and services.</p></div>
      </div>
      <div class="about-item">
        <span class="circle-icon"><svg width="20" height="14" viewBox="0 0 20 14"><path d="M2 12 10 4l8 8" fill="none" stroke="#fff" stroke-width="3"/></svg></span>
        <div><h4>Partnership</h4><p>VELMOR negotiates and supports a lot of private events and parties for our members.</p></div>
      </div>
      <div class="about-item">
        <span class="circle-icon"><svg width="20" height="14" viewBox="0 0 20 14"><path d="M2 12 10 4l8 8" fill="none" stroke="#fff" stroke-width="3"/></svg></span>
        <div><h4>About VELMOR</h4><p>VELMOR is a luxury lifestyle club focused on access to the best services, trusted experts and rewarding experiences.</p></div>
      </div>
    </div>
  </section>

  <section class="team">
    <h2>OUR TEAM</h2>
    <p class="lead">Morbi leo risus, porta ac consectetur ac, vestibulum at eros.</p>
    <div class="team-grid">
      <article class="member">
        <div class="member-photo" role="img" aria-label="Portrait of team member Aldo Renn"></div>
        <span class="up"><svg width="20" height="14" viewBox="0 0 20 14"><path d="M2 12 10 4l8 8" fill="none" stroke="#fff" stroke-width="3"/></svg></span>
        <h4>Aldo Renn</h4>
        <p>Morbi leo risus, porta ac consectetur ac, vestibulum at eros. Lorem ipsum dolor sit amet, consectetur adipiscing elit.</p>
      </article>
      <article class="member featured">
        <div class="member-photo" role="img" aria-label="Portrait of team member Piers Halden"></div>
        <span class="up"><svg width="20" height="14" viewBox="0 0 20 14"><path d="M2 12 10 4l8 8" fill="none" stroke="#fff" stroke-width="3"/></svg></span>
        <h4>Piers Halden</h4>
        <p>Morbi leo risus, porta ac consectetur ac, vestibulum at eros. Lorem ipsum dolor sit amet, consectetur adipiscing elit.</p>
        <div class="socials"><span></span><span></span><span></span></div>
      </article>
      <article class="member">
        <div class="member-photo" role="img" aria-label="Portrait of team member Nadia Orwell"></div>
        <span class="up"><svg width="20" height="14" viewBox="0 0 20 14"><path d="M2 12 10 4l8 8" fill="none" stroke="#fff" stroke-width="3"/></svg></span>
        <h4>Nadia Orwell</h4>
        <p>Morbi leo risus, porta ac consectetur ac, vestibulum at eros. Lorem ipsum dolor sit amet, consectetur adipiscing elit.</p>
      </article>
      <article class="member">
        <div class="member-photo" role="img" aria-label="Portrait of team member Marcus Lyle"></div>
        <span class="up"><svg width="20" height="14" viewBox="0 0 20 14"><path d="M2 12 10 4l8 8" fill="none" stroke="#fff" stroke-width="3"/></svg></span>
        <h4>Marcus Lyle</h4>
        <p>Morbi leo risus, porta ac consectetur ac, vestibulum at eros. Lorem ipsum dolor sit amet, consectetur adipiscing elit.</p>
      </article>
      <article class="member">
        <div class="member-photo" role="img" aria-label="Portrait of team member Irena Vasko"></div>
        <span class="up"><svg width="20" height="14" viewBox="0 0 20 14"><path d="M2 12 10 4l8 8" fill="none" stroke="#fff" stroke-width="3"/></svg></span>
        <h4>Irena Vasko</h4>
        <p>Morbi leo risus, porta ac consectetur ac, vestibulum at eros. Lorem ipsum dolor sit amet, consectetur adipiscing elit.</p>
      </article>
      <article class="member">
        <div class="member-photo" role="img" aria-label="Portrait of team member Claire Dunmore"></div>
        <span class="up"><svg width="20" height="14" viewBox="0 0 20 14"><path d="M2 12 10 4l8 8" fill="none" stroke="#fff" stroke-width="3"/></svg></span>
        <h4>Claire Dunmore</h4>
        <p>Morbi leo risus, porta ac consectetur ac, vestibulum at eros. Lorem ipsum dolor sit amet, consectetur adipiscing elit.</p>
      </article>
    </div>
  </section>

  <section class="membership">
    <div class="membership-photo" role="img" aria-label="Evening view over a resort terrace and pool"></div>
    <div class="shade"></div>
    <div class="inner">
      <h3>VELMOR</h3>
      <h2>Membership provides you with amazing benefits<br>and services.</h2>
      <span class="btn">VISIT</span>
    </div>
  </section>

  <section class="band-title testi-head">
    <h2>TESTIMONIALS</h2>
    <p class="lead">Dummy text of the printing and typesetting</p>
  </section>

  <section class="testimonial">
    <div class="testi-photo" role="img" aria-label="Sailing yacht on the sea at sunset"></div>
    <p class="testi-quote">Lorem Ipsum is simply dummy text of the printing and typesetting industry. Lorem Ipsum has been the industry's standard dummy text ever since the 1500s, when an unknown printer took a galley of type and scrambled it to make a type specimen book. It has survived not only five centuries, but also the leap into electronic typesetting, remaining.</p>
    <div class="roles">
      <div class="role active"><small>Lead Partner</small><strong>Co-Founder</strong></div>
      <div class="role"><small>Club Director</small><strong>Founder</strong></div>
      <div class="role"><small>Member Relations</small><strong>Manager</strong></div>
    </div>
  </section>

  <footer class="footer">
    <div class="footer-col">
      <h4>VELMOR</h4>
      <p>VELMOR is a luxury lifestyle club for members who value trusted advice and exceptional service.</p>
      <div class="footer-socials"><span></span><span></span><span></span><span></span></div>
    </div>
    <div class="footer-col">
      <h4>Contact us</h4>
      <p>1420 Harbor Crest Drive, Suite 60<br>Naples, FL 34102<br>Phone: +1 555 0148 2290<br>hello@velmor.example</p>
    </div>
    <div class="footer-col">
      <h4>Newsletter</h4>
      <p>Sign up to receive news about new benefits and member events.</p>
      <div class="subscribe"><span>Your email</span><b></b></div>
    </div>
  </footer>
  <div class="bottom-bar"><svg width="20" height="12" viewBox="0 0 20 12"><path d="M2 10 10 2l8 8" fill="none" stroke="#fff" stroke-width="3"/></svg></div>

</div>
</body>
</html>
```